Letterhead and matching envelope design for a dental office

We need a new stationary design, letterhead and envelope #10, for a dental office in Denver area. We are called Bright Harbor Dental. We want a simple and minimalistic design but not a boring design. I wish to have one good point that makes it look professional. I have attached our logo. Feel free to use either one. I want the design for letterhead and envelope look like a "matching pair" but not look the same. The envelope doesn't have to be white and it will have an address window on bottom left.

Target Market(s)

everyone who visits dentist (adults)

Industry/Entity Type

Dental

Font styles to use
Other font styles liked:
• close to font on logo or something that matches well

Requirements
Must have
• professional
• simple, minimalistic
• unique point that stands out
Nice to have
• matching but not same design for letterhead and envelope
Should not have
• not look like all the other boring designs
• no flowery, distracting feats

```html
<!DOCTYPE html>
<html lang="en">
<head>
<meta charset="utf-8">
<title>Bright Harbor Dental Stationery</title>
<link rel="stylesheet" href="https://fonts.googleapis.com/css2?family=Open+Sans:wght@400;600&display=swap">
<style>
  :root {
    --brand-green: #43b549;
    --ink: #3a3a3a;
    --rule: #8a8a8a;
    --paper: #ffffff;
    --backdrop: #b8b8b8;
  }
  * { margin: 0; padding: 0; box-sizing: border-box; }
  html, body { width: 1200px; height: 1200px; overflow: hidden; }
  body {
    position: relative;
    background: var(--backdrop);
    font-family: "Open Sans", Arial, sans-serif;
    color: var(--ink);
  }
  .sheet { position: absolute; background: var(--paper); }

  /* Letterhead */
  .letterhead { left: 29px; top: 182px; width: 618px; height: 875px; }
  .brand-mark {
    position: absolute;
    display: flex; flex-direction: column; align-items: center; gap: 8px;
    color: var(--brand-green); font-weight: 600; text-align: center;
    letter-spacing: 0.12em; text-transform: uppercase;
  }
  .letterhead .brand-mark { left: 0; right: 0; top: 62px; font-size: 17px; }
  .brand-dot { width: 40px; height: 40px; border-radius: 50%; background: var(--brand-green); }
  .letterhead-footer {
    position: absolute; left: 38px; right: 38px; top: 822px;
    border-top: 1px solid var(--rule);
    padding-top: 8px; text-align: center; font-size: 10.5px; line-height: 1.3;
  }
  .footer-name { color: var(--brand-green); text-transform: uppercase; }
  .footer-address { text-transform: uppercase; }
  .footer-label { color: var(--brand-green); }
  .footer-sep { color: var(--brand-green); padding: 0 4px; }

  /* Envelope back */
  .envelope-back { left: 612px; top: 385px; width: 558px; height: 267px; }
  .envelope-flap { position: absolute; left: 0; top: 0; width: 558px; height: 73px; }
  .flap-url {
    position: absolute; left: 0; right: 0; top: 29px;
    text-align: center; color: var(--paper); font-size: 11.5px;
  }

  /* Envelope front */
  .envelope-front { left: 612px; top: 663px; width: 558px; height: 267px; }
  .envelope-front .brand-mark { left: 18px; top: 32px; width: 110px; font-size: 11px; gap: 6px; }
  .envelope-front .brand-dot { width: 26px; height: 26px; }
  .return-address {
    position: absolute; left: 22px; top: 193px;
    font-size: 9.5px; line-height: 1.15;
  }
  .contact-list { list-style: none; margin-top: 6px; }
  .contact-list li { display: flex; align-items: center; gap: 5px; height: 13px; }
  .contact-list svg { width: 8px; height: 8px; fill: var(--brand-green); }
</style>
</head>
<body>

  <section class="sheet letterhead">
    <div class="brand-mark">
      <span class="brand-dot"></span>
      <span>Bright Harbor Dental</span>
    </div>
    <footer class="letterhead-footer">
      <div class="footer-name">Bright Harbor Dental</div>
      <div class="footer-address">4820 Lakeview Pkwy Suite 210 Arvada CO 80003</div>
      <div><span class="footer-label">P:</span> 720-555-0148<span class="footer-sep">|</span><span class="footer-label">E:</span> hello@brightharbor.com<span class="footer-sep">|</span><span class="footer-label">W:</span> www.brightharbordental.com</div>
    </footer>
  </section>

  <section class="sheet envelope-back">
    <svg class="envelope-flap" viewBox="0 0 558 73" aria-hidden="true">
      <polygon points="0,0 558,0 524,73 34,73" fill="var(--brand-green)"/>
    </svg>
    <div class="flap-url">www.brightharbordental.com</div>
  </section>

  <section class="sheet envelope-front">
    <div class="brand-mark">
      <span class="brand-dot"></span>
      <span>Bright Harbor Dental</span>
    </div>
    <address class="return-address" style="font-style:normal">
      <div>4820 Lakeview Pkwy Suite 210</div>
      <div>Arvada , CO 80003</div>
      <ul class="contact-list">
        <li><svg viewBox="0 0 10 10"><path d="M2 0.5 L4 2.5 L3 4 Q4.5 6 6 7 L7.5 6 L9.5 8 L8 9.5 Q3 9 0.5 2 Z"/></svg>720-555-0148</li>
        <li><svg viewBox="0 0 10 10"><path d="M0 2 H10 V8.5 H0 Z M0.8 2.6 L5 5.8 L9.2 2.6" stroke="#fff" stroke-width="0.9"/></svg>hello@brightharbor.com</li>
        <li><svg viewBox="0 0 10 10"><circle cx="5" cy="5" r="4.3" fill="none" stroke="var(--brand-green)" stroke-width="1"/><path d="M0.7 5 H9.3 M5 0.7 V9.3" stroke="var(--brand-green)" stroke-width="0.8"/></svg>www.brightharbordental.com</li>
      </ul>
    </address>
  </section>

</body>
</html>
```